Brand and Marketing Coach Needs PDF Designed

I have content that i need placed into a simple but great PDF design. The PDF is about the formula I use to build personal brands. This is geared towards entrepreneurs, experts, coaches, therapists, wellness practitioners, and indpendent business owners who serve to improve the lives of others.
The company name is changing from TorvelCast to Selling with the Village (I don't have that logo yet, so working backwards a bit. For now, the TorvelCast logo can be used.) My brand is NOT formal and corporate, but it's also not neon-pink and screaming at you. It's down to earth, hip, a bit modern but warm. It's about no BS and authenticity. The final deliverable should make the reader feel focused, smart, motivated and hopeful.

Target Market(s)

Conscious entrepreneurs and small business owners. this one is specifically for pharmacy entrepreneurs but this will be used for various audiences later.

Font styles to use
Sans Serif

Colors
eaf1f7
3377b5
6b449b
f37122
faa54b
f68e4e
ffc214

Requirements
Must have
• Modern design. colors that match logo - 4e5583 (i think that is the blue.) d65a40.
• Could have these colors as well: c6a254, 01bcc3
• But open to other colors
Nice to have
• I'd like to see some ways to make this PDF simple and readable, and eye-catching. I'd also like to use the uploaded ebooks for design ideas.
Should not have
• neon colors, clip art

```html
<!DOCTYPE html>
<html lang="en">
<head>
<meta charset="utf-8">
<title>The True Story Method – 30 page layout</title>
<link href="https://fonts.googleapis.com/css2?family=Cormorant+Garamond:ital,wght@0,400;0,600;1,400&family=Great+Vibes&family=Archivo:wght@800&display=swap" rel="stylesheet">
<style>
:root{
  --page:#4f5482;
  --page-deep:#464b78;
  --ink:#ffffff;
  --ink-soft:rgba(255,255,255,.85);
  --field:#ffffff;
  --line:rgba(255,255,255,.75);
  --canvas:#ffffff;
  --alert:#e3001b;
  --photo-a:#6b5a78;
  --photo-b:#b0674f;
  --star-a:#8a6fc0;
  --star-b:#c35a7a;
}
*{box-sizing:border-box;margin:0;padding:0}
html,body{width:819px;height:1200px;overflow:hidden;background:var(--canvas)}
body{position:relative;font-family:"Cormorant Garamond",Georgia,serif;color:var(--ink)}
.page{position:absolute;width:185px;height:141px;background:var(--page);padding:9px 11px;overflow:hidden}
.c1{left:31px}.c2{left:221px}.c3{left:410px}.c4{left:598px}
.r1{top:11px}.r2{top:159px}.r3{top:306px}.r4{top:454px}.r5{top:601px}.r6{top:748px}.r7{top:895px}.r8{top:1042px}
.body{font-size:2.8px;line-height:3.5px;color:var(--ink-soft);margin-bottom:2.5px}
.body b{color:var(--ink)}
.kicker{font-size:2.8px;line-height:3.3px;margin-bottom:4px;color:var(--ink-soft);font-style:italic}
.foot{position:absolute;bottom:4px;left:0;right:0;text-align:center;font-size:2.2px;color:var(--ink-soft)}
.title-caps{font-size:17px;font-weight:400;letter-spacing:.3px;margin-bottom:5px;font-variant:small-caps;line-height:1}
.chapter{position:absolute;inset:0;display:flex;flex-direction:column;align-items:center;justify-content:center;text-align:center;font-size:15.5px;line-height:19px;letter-spacing:.3px}
.chapter .num{display:block;font-size:36px;line-height:40px;margin-bottom:2px}
.tagline{font-family:"Great Vibes",cursive;font-size:10px;text-align:center}
.sec{display:flex;align-items:center;gap:4px;font-size:6.5px;margin-bottom:4px}
.sec i{display:inline-flex;width:8px;height:8px;border-radius:50%;background:var(--ink);color:var(--page);font-style:normal;font-size:5px;align-items:center;justify-content:center}
.lead{font-size:3.2px;font-weight:600;line-height:3.8px;margin-bottom:2px}
.field{background:var(--field);height:8px;margin:2px 0 4px}
.field.tall{height:18px}
.field.xl{height:26px}
.prompt{font-size:2.5px;line-height:3.1px;font-style:italic;color:var(--ink-soft)}
.grid2{display:grid;grid-template-columns:1fr 1fr;gap:1px 2px}
.grid2 span{border:0.5px solid var(--line);height:5px}
.table{display:grid;grid-template-columns:1.2fr 1fr 1fr;font-size:2.2px;color:var(--ink-soft)}
.table span{border:0.5px solid var(--line);height:5.5px;padding:1px;text-align:right}
.table .hd{background:var(--field);color:var(--page);text-align:center}
.table .blank{border:none}
.cols3{display:grid;grid-template-columns:1fr 1fr 1fr;gap:2px;height:60px}
.cols3 span{background:var(--field)}
.photo{position:absolute;background:linear-gradient(160deg,var(--photo-a),var(--photo-b) 55%,var(--page-deep))}
.star{position:absolute;background:radial-gradient(circle,var(--star-b),var(--star-a) 45%,transparent 72%)}
.contact{font-size:2.4px;display:flex;align-items:center;gap:2px;margin:1px 0}
.contact i{width:3px;height:3px;border-radius:50%;background:var(--ink);display:inline-block}
.cover{text-align:center}
.cover-title{margin-top:22px;font-weight:400;line-height:1}
.cover-title .small{display:block;font-size:7px;letter-spacing:1px}
.cover-title .big{display:block;font-size:17px;letter-spacing:.6px;margin:2px 0}
.cover-sub{font-size:6px;margin-top:22px}
.cover-note{font-size:3.6px;font-style:italic;line-height:4.2px}
.done{position:absolute;left:460px;top:1068px;width:313px;text-align:center;font-family:"Archivo",Arial,sans-serif;font-weight:800;color:var(--alert);font-size:47px;line-height:46px}
</style>
</head>
<body>

<section class="page c1 r1 cover">
  <h1 class="cover-title">
    <span class="small">THE</span>
    <span class="big">TRUE STORY</span>
    <span class="small">METHOD</span>
  </h1>
  <div class="cover-sub">For Pharmacy Entrepreneurs</div>
  <div class="cover-note">The quick n' dirty guide to creating a unique personal brand<br>that attracts your ideal clients.</div>
</section>

<section class="page c2 r1">
  <div class="tagline">Your business has a story to tell.</div>
  <div class="photo" role="img" aria-label="Portrait photograph of the brand coach" style="left:40px;top:28px;width:105px;height:113px"></div>
</section>

<section class="page c3 r1">
  <p class="kicker">I'm so glad you're here! Before we start, a few things:</p>
  <h2 class="title-caps">What this is:</h2>
  <p class="body">The True Story Method is the exact map I use to build an honest brand for any business. It is simple, useful and fast.</p>
  <p class="body">Most owners skip branding and jump to tactics. This guide starts with who you are, so your marketing finally feels like you.</p>
  <p class="body">This is what most people don't tell you about the real work that happens in the background.</p>
  <p class="body">When you go through the steps, you will see your brand clearly and know how to speak to clients you love.</p>
  <p class="foot">page 3 of 30</p>
</section>

<section class="page c4 r1">
  <p class="kicker">I'm so glad you're here! Before we start, a few things:</p>
  <h2 class="title-caps">Who this is for:</h2>
  <p class="body">This method is for you if you're a pharmacy owner who is starting out or growing a store and wants a brand that feels real.</p>
  <p class="body">If you already have a business but feel unseen by the clients you want most, this is your next step.</p>
  <p class="body">If you're new, you'll save time and money by getting this right before you spend on ads.</p>
  <p class="body">Long story short, you're ready to step it up, get noticed, and grow your client base.</p>
  <p class="foot">page 4 of 30</p>
</section>

<section class="page c1 r2"><div class="chapter"><span class="num">1</span>START HERE</div></section>

<section class="page c2 r2">
  <p class="lead">Freedom, impact, and profit…</p>
  <p class="body">One or all of these are the reasons you started. But right now you're wondering how to stand out from all the noise online.</p>
  <p class="body">Social feeds are crowded and every business seems to say the same thing in the same voice, so clients scroll past.</p>
  <p class="body">Because that is COMPLETELY BACKWARDS. You can't pick tactics before you know your story and the people you serve.</p>
  <p class="body">Writing your website copy without knowing how to stand apart leaves you guessing and your ideal clients lost.</p>
  <p class="body">When I ask owners to do this, their eyes light up. They finally see what makes them different and worth choosing.</p>
  <p class="body">This is the way to build a strong and authentic brand.</p>
  <p class="foot">page 6 of 30</p>
</section>

<section class="page c3 r2"><div class="chapter"><span class="num">2</span>WHAT IS<br>BRANDING,<br>ANYWAY?</div></section>

<section class="page c4 r2">
  <p class="lead">BRANDING IS NOT</p>
  <p class="body">Branding is NOT your logo, colors and fonts. That is visual branding, and it only works once the core is clear.</p>
  <p class="lead">BRANDING IS</p>
  <p class="body">Branding is how you make someone feel after they've heard you talk, read your blog post or visited your store.</p>
  <p class="body">Your brand has an essence, a personality and a distinct way of communicating that people remember.</p>
  <p class="body" style="text-align:center;font-style:italic">"Your brand is what people say about you when you're not in the room." — R. Ellison, retail founder</p>
  <p class="body">When people know and trust your brand, they become clients. To have a credible brand you need:</p>
  <p style="text-align:center;font-size:3.2px;line-height:5px;font-weight:600">WHO YOU ARE<br>WHAT YOU DO<br>HOW YOU DO IT</p>
</section>

<section class="page c1 r3">
  <p class="body" style="margin-top:14px">Your personal brand will define how you present yourself on all your marketing platforms — on and offline. It's everything you and your team say and do.</p>
  <p class="body">Without a brand, you fade into online oblivion.</p>
  <p class="body">This is your foundation and the BLUEPRINT for all you do.</p>
  <p class="foot">page 9 of 30</p>
</section>

<section class="page c2 r3"><div class="chapter"><span class="num">3</span>FOLLOW THE<br>TRUE STORY<br>METHOD</div></section>

<section class="page c3 r3">
  <div class="sec"><i>1</i>MOTIVATORS</div>
  <p class="lead">Your WHY and the real reason you created this business.</p>
  <p class="body">This is what motivates you to serve people as you do, and the purpose behind your business. Your values shape every choice you make.</p>
  <p class="body">Similar to core values, motivators come from who you are. Naming them helps clients feel why you care.</p>
  <p class="prompt">What is your WHY: the real reason the vision of this business exists?</p>
  <div class="field"></div>
  <p class="prompt">What do you passionately stand for?</p>
  <div class="field"></div>
  <p class="foot">page 11 of 30</p>
</section>

<section class="page c4 r3">
  <p class="prompt">What do you believe — what's your philosophy — and how is that different from others in your field?</p>
  <div class="field"></div>
  <p class="lead" style="margin-top:4px">Your Motivators:</p>
  <p class="prompt">From the answers above, choose 3–4 phrases that stand out and write them here.</p>
  <div class="grid2" style="margin-top:2px"><span></span><span></span><span></span><span></span><span></span><span></span></div>
  <p class="foot">page 12 of 30</p>
</section>

<section class="page c1 r4">
  <div class="sec"><i>2</i>VALUE</div>
  <p class="lead">Your expertise and the results your clients get from working with you.</p>
  <p class="body">Your prospects must understand what you do and what you're asking them to do. Be clear about the change you create.</p>
  <p class="prompt">What is your expertise: what do you consider yourself to be the authority on?</p>
  <div class="field"></div>
  <p class="prompt">How do you do this in a way that is different from others in your industry?</p>
  <div class="field tall"></div>
  <p class="foot">page 13 of 30</p>
</section>

<section class="page c2 r4">
  <p class="prompt">How does a client feel after working with you?</p>
  <div class="field"></div>
  <p class="prompt">Why should anyone choose to do business with you over anyone else in your market space?</p>
  <div class="field"></div>
  <p class="lead" style="margin-top:3px">Your Value:</p>
  <p class="prompt">From the answers above, choose 2–3 sentences that stand out and write them here.</p>
  <div class="field tall"></div>
  <p class="foot">page 14 of 30</p>
</section>

<section class="page c3 r4">
  <div class="sec"><i>3</i>Your Ideal Client</div>
  <p class="lead">The client for whom you absolutely know you can serve at the highest level, and positively impact.</p>
  <p class="body">Your ideal client must recognize themselves in you. Know their needs, values and habits so your message lands.</p>
  <p class="body">A bit more work goes into discovering your ideal client. This is only a fraction of it, but it's a great start.</p>
  <div class="table" style="margin-top:3px">
    <span class="blank"></span><span class="hd">YOUR CLIENT</span><span class="hd">VALUE THAT ALIGN</span>
    <span>Male/female/other</span><span></span><span></span>
    <span>Age range</span><span></span><span></span>
    <span>Education level</span><span></span><span></span>
  </div>
  <p class="foot">page 15 of 30</p>
</section>

<section class="page c4 r4">
  <div class="table">
    <span class="blank"></span><span class="hd">YOUR CLIENT</span><span class="hd">VALUE THAT ALIGN</span>
    <span>Income level</span><span></span><span></span>
    <span>Biggest aspiration</span><span></span><span></span>
    <span>Where do they live</span><span></span><span></span>
    <span>What they really want</span><span></span><span></span>
    <span>What core values</span><span></span><span></span>
    <span>What wrong opinions</span><span></span><span></span>
  </div>
  <p class="prompt" style="margin-top:6px">Now, from the above, choose 3 words that stand out most about your ideal client.</p>
  <div class="field"></div>
  <p class="foot">page 16 of 30</p>
</section>

<section class="page c1 r5">
  <div class="sec"><i>4</i>Positioning / Representation</div>
  <p class="lead">The strategy you create to establish yourself as the expert, emphasizing ways in which you are unique to others in your industry.</p>
  <p class="body">To have a successful business that attracts the clients you love, you must position yourself as the go-to expert.</p>
  <p class="body"><b>Knowing how to position yourself guides and simplifies all of your marketing.</b></p>
  <p class="prompt">What do your products or services look like? Are they different from what is out there?</p>
  <div class="field xl"></div>
  <p class="foot">page 17 of 30</p>
</section>

<section class="page c2 r5">
  <p class="prompt">How does the look of these products or services represent you and what set of personalities do they attract?</p>
  <div class="field xl" style="margin-top:3px"></div>
  <p class="lead">What you represent:</p>
  <p class="prompt">From the answers above, choose 3–4 words or phrases that stand out most to you.</p>
  <div class="grid2" style="margin-top:2px"><span></span><span></span><span></span><span></span><span></span><span></span></div>
  <p class="foot">page 18 of 30</p>
</section>

<section class="page c3 r5">
  <div class="sec"><i>5</i>Your Story</div>
  <p class="lead">The relatable circumstances that brought you to create this business and run it the way you do.</p>
  <p class="body">Your story makes you human, unique and relatable. It shows how your situation led you to create this business.</p>
  <p class="body">Because it's likely that if you have this fault or feel this thing, then there are so many others who have it too.</p>
  <p class="prompt">List 1–3 things that are true about you now or about how you got to where you are.</p>
  <div class="grid2" style="margin-top:3px;grid-template-columns:1fr"><span></span><span></span><span></span></div>
  <p class="foot">page 19 of 30</p>
</section>

<section class="page c4 r5">
  <div class="sec"><i>6</i>Personality / Your Character</div>
  <p class="lead">Of course you have a personality, but this is all about how you relay that, as a brand, to attract clients who are a great fit.</p>
  <p class="body">Your brand personality goes beyond just saying you're a fun and lighthearted person. It shows in every post and every visit.</p>
  <p class="body">This is about your approach and the impact you have on your clients.</p>
  <p class="prompt">What do you want your ideal client to feel after reading your post or walking into your store?</p>
  <div class="field tall"></div>
  <p class="foot">page 20 of 30</p>
</section>

<section class="page c1 r6">
  <p class="prompt">Ask three people you know what they think is great and unique about you. Really, email them and ask.</p>
  <p class="lead">Write 1–3 things that people you know consider to be great and unique about you.</p>
  <div class="grid2"><span></span><span></span></div>
  <p class="prompt" style="margin-top:2px">What do you want people to say behind your back?</p>
  <div class="field"></div>
  <p class="prompt">YOUR MOST MEMORABLE THING ABOUT YOU. What's the weirdest thing about you?</p>
  <p class="lead">Write 1–3 things that are most memorable about you, that you hear friends say often.</p>
  <div class="grid2"><span></span><span></span></div>
  <p class="foot">page 21 of 30</p>
</section>

<section class="page c2 r6">
  <div class="sec"><i>7</i>Communication Style</div>
  <p class="lead">The way you speak and how you engage with your audience.</p>
  <p class="body">Building a brand and producing great content to generate awareness takes more than clear communication. Your words must sound like you.</p>
  <p class="body">When language on your site is stiff, people notice. Speak the way you speak in real life, and clients relax.</p>
  <p class="body">So you either reach them, or don't use them. With that in mind, pick three words or expressions you use often.</p>
  <p class="body">Just may be unique — your phrases, your jokes, your warmth — is what people remember.</p>
  <p class="foot">page 22 of 30</p>
</section>

<section class="page c3 r6">
  <p class="lead">3 Words, phrases, or messages that you use over and over again:</p>
  <div class="cols3"><span></span><span></span><span></span></div>
  <p class="prompt" style="margin-top:4px">How do you speak to your audience? When you communicate what do you give off?</p>
  <div class="field tall"></div>
  <p class="foot">page 23 of 30</p>
</section>

<section class="page c4 r6">
  <div class="sec"><i>8</i>Authenticity / Transparency</div>
  <p class="lead">Being human. Being real. Being transparent.</p>
  <p class="body">I believe that when you bring yourself — your most authentic self — to your business, you attract the clients you want most.</p>
  <p class="body">The final piece I'm sharing with you is about transparency. People trust a brand that shows its real face and real process.</p>
  <p class="body">This is why so many are scared to be so honest. Sharing the messy middle is what earns loyalty.</p>
  <p class="body">Back then, I had a bigger goal and social media wasn't the same. Real connection is what grew the business.</p>
  <p class="foot">page 24 of 30</p>
</section>

<section class="page c1 r7">
  <p class="lead">Guess what does . . .</p>
  <p class="body">Well, it becomes part of your brand. And possibly one of the most important things any business and expert can do to become a leader.</p>
  <p class="body">So my question to you is are you willing to be transparent or are you going to play the game where you never show up?</p>
  <p class="body">If you're not willing to be transparent, there's only so much success you'll have online.</p>
  <div class="star" role="img" aria-label="Decorative hand-drawn star illustration" style="left:18px;top:68px;width:58px;height:58px"></div>
  <p class="foot">page 25 of 30</p>
</section>

<section class="page c2 r7">
  <div class="sec"><i>9</i>Trust</div>
  <p class="lead">People buy from and do business with people they trust, but you must also trust in your own genius and expertise.</p>
  <p class="body">Creating trust with your followers requires you to pay close attention to what you say, do and offer. This is built on integrity.</p>
  <p class="body">This final piece may be the toughest for some of you. Because it is so intensely personal, trust in yourself comes first.</p>
  <p class="body">You may need to do some mindset work, yoga, meditation… whatever it is that can get you centered.</p>
  <p class="foot">page 26 of 30</p>
</section>

<section class="page c3 r7">
  <p class="lead">Now, never ever try to be someone you're not.</p>
  <p class="body">Because that will backfire. That's what this is all about and why you should go through this tool in its entirety.</p>
  <p class="body">It doesn't mean you walk around with this massive ego and attitude. It simply means you own the value you bring.</p>
  <p class="body">What happens is they start hearing that while they are creating this amazing brand and business.</p>
  <p class="body">Doesn't that sound much better than fitting into someone else's brain, body and brand and convincing yourself?</p>
  <p class="foot">page 27 of 30</p>
</section>

<section class="page c4 r7"><div class="chapter" style="font-size:17px;line-height:20px;padding-top:24px">WHAT'S<br>NEXT?</div></section>

<section class="page c1 r8">
  <p class="lead">This is just the tip of the iceberg.</p>
  <p class="body">1. In the days to come, I'm going to help you begin creating your authentic personal brand. Be sure to check your email.</p>
  <p class="body">2. Meanwhile, treat yourself to one hour with each step of the True Story Method you already have under your belt.</p>
  <p class="body">3. Email me with any burning questions you have at dana@torvelcast.example. I'll reply directly to you.</p>
  <p class="foot">page 29 of 30</p>
</section>

<section class="page c2 r8">
  <div class="photo" role="img" aria-label="Portrait photograph of the author holding a laptop" style="left:11px;top:9px;width:52px;height:62px"></div>
  <div style="margin-left:58px">
    <p class="lead">ABOUT ME</p>
    <p class="body">I'm Dana Whitlow, Founder, and CEO of TorvelCast — Selling with the Village.</p>
    <p class="body">As a marketing strategist and coach, I help conscious owners build brands that feel honest and warm.</p>
    <p class="body">I believe that you can reach your goals and get people talking about your message.</p>
  </div>
  <p class="body" style="margin-top:4px">When I walked away from my job as a marketing director to start my own business, I never looked back.</p>
  <p class="body">The real reason I created my business was to do what I love with people I adore.</p>
  <p style="font-size:3px;font-style:italic;position:absolute;left:50px;bottom:10px">Connect with me:</p>
  <div style="position:absolute;left:96px;bottom:6px">
    <p class="contact"><i></i>torvelcast.example/social</p>
    <p class="contact"><i></i>torvelcast.example/photos</p>
    <p class="contact"><i></i>dana@torvelcast.example</p>
  </div>
</section>

<div class="done">DONE!<br>30 PAGES</div>

</body>
</html>
```